House flipping business web site needed

pinecrestholdingsgroup.example.
I am a residential developer in Northern NJ and I am looking for a fresh new updated website. I have an intro video about my company being made now. I don't update it very often but I want an easy format that I can add update photos to on projects I have worked on or homes I renovate for sale.

Target Market(s)

investors into my projects so a portfolio , people looking to sell their homes to me.

Industry/Entity Type

Real Estate Development

Number of Pages Required

4 page

Font styles to use
Serif

Colors
33b8a4
39a9d7
cadf82

Requirements
Must have
• space for an intro video about my company
• a portfolio with pictures and information about each project
• Markets we serve- Morris County, NJ
• My logo- already created
• SEO
• Yes I would like this to function over all platforms. Phone, computer, all platforms.
• history and background page
• I am looking for a completed page that I can upload to the site that hosts my website
Nice to have
• I want something creative, easy to navigate. modern.

```html
<!DOCTYPE html>
<html lang="en">
<head>
<meta charset="utf-8">
<title>Pinecrest Holdings Group – Builders and Renovators</title>
<link rel="stylesheet" href="https://fonts.googleapis.com/css2?family=Lora:wght@500;600;700&family=Source+Serif+4:opsz,wght@8..60,300;8..60,400;8..60,600&display=swap">
<style>
:root{
  --teal:#33b8a4;
  --blue:#39a9d7;
  --lime:#cadf82;
  --teal-deep:#2a9e8d;
  --ink:#1f2a2c;
  --muted:#55615f;
  --paper:#ffffff;
  --mist:#f2f5f3;
  --line:#d6dedb;
  --head:'Lora',Georgia,serif;
  --body:'Source Serif 4',Georgia,serif;
}
*{box-sizing:border-box;margin:0;padding:0}
html,body{width:1200px;height:2378px;overflow:hidden}
body{font-family:var(--body);color:var(--ink);background:var(--paper);position:relative}
h1,h2,h3,h4{font-family:var(--head)}
.band-gradient{background:linear-gradient(100deg,var(--teal),var(--blue))}

/* hero */
.hero{position:relative;height:552px;overflow:hidden}
.hero-photo{position:absolute;inset:0;background:linear-gradient(120deg,#d8d4c6 0%,#b9ae93 30%,#cfc7b8 55%,#9c8f80 75%,#e2e2e2 100%)}
.topbar{position:absolute;top:0;left:0;right:0;height:34px;border-bottom:1px solid rgba(255,255,255,.6);display:flex;align-items:center;padding:0 52px;color:#fff;font-size:13px}
.topbar .contact-item{display:flex;align-items:center;gap:8px;margin-right:28px}
.topbar .spacer{flex:1}
.sell-btn{background:#fff;color:var(--teal-deep);font-size:12px;font-weight:600;padding:3px 8px;border-radius:4px;margin-right:20px}
.social-dot{width:9px;height:9px;border-radius:50%;background:#fff;margin-left:20px}
.brand{position:absolute;left:62px;top:46px;width:180px;display:flex;flex-direction:column;align-items:center;gap:12px;color:#fff}
.brand-mark{width:60px;height:60px;border-radius:50%;background:var(--lime)}
.brand-name{font-family:var(--head);font-size:21px;font-weight:500;letter-spacing:2px;text-align:center;line-height:1.15}
.nav{position:absolute;right:50px;top:56px;display:flex;gap:34px;font-family:var(--head);font-size:15px;font-weight:600;color:#fff}

/* welcome */
.welcome{height:193px;text-align:center;color:#fff;padding:20px 60px 0}
.welcome h1{font-size:22px;font-weight:700;padding-bottom:14px;border-bottom:1px dashed rgba(255,255,255,.85);margin:0 -20px 16px}
.welcome p{font-size:12.5px;line-height:20px;margin-bottom:14px}

/* builders */
.builders{height:409px;background:var(--mist);text-align:center;padding-top:24px}
.section-title{font-size:22px;font-weight:700;color:var(--ink)}
.section-title span{color:var(--teal)}
.dotted-rule{border-bottom:1px dotted var(--teal);margin:14px 40px 0}
.features{display:flex;justify-content:space-between;padding:40px 52px 0}
.feature{width:340px}
.feature-icon{width:76px;height:76px;margin:0 auto 10px;border-radius:4px;background:linear-gradient(135deg,var(--teal),var(--blue));display:flex;align-items:center;justify-content:center}
.feature h3{font-size:17px;font-weight:700;margin-bottom:16px}
.feature p{font-size:12.5px;line-height:20px;color:var(--muted);font-weight:300}

/* mail + video */
.mail-video{display:flex;height:328px}
.mail{width:600px;padding:30px 49px 0;text-align:center;color:#fff}
.mail h2{font-size:26px;font-weight:600;margin-bottom:18px}
.field{background:#fff;border-radius:3px;color:#7d8886;font-size:12px;height:32px;display:flex;align-items:center;justify-content:center;margin-bottom:18px}
.field-row{display:flex;gap:18px}
.field-row .field{flex:1}
.field.message{height:56px;align-items:flex-start;padding-top:10px}
.send-btn{display:inline-block;background:#fff;color:var(--ink);font-size:12.5px;font-weight:600;padding:9px 19px;border-radius:3px}
.video{position:relative;width:600px;background:linear-gradient(180deg,#8ec3ee 0%,#d6e9f7 30%,#4c6a3a 50%,#2f4a52 70%,#1e3640 100%)}
.play{position:absolute;left:233px;top:100px}

/* work */
.work{height:420px;text-align:center;padding-top:8px}
.work .dotted-rule{margin:14px 52px 0}
.projects{display:flex;gap:28px;padding:44px 52px 0}
.project{width:253px}
.project-photo{height:206px}
.project h3{font-size:17px;font-weight:600;margin:26px 0 14px}
.project p{font-size:12.5px;line-height:20px;color:var(--muted);font-weight:300}

/* like bar */
.like-bar{height:71px;background:var(--mist);position:relative}
.like-bar::before{content:"";position:absolute;left:66px;right:66px;top:35px;border-top:1px solid var(--line)}
.like-pill{position:absolute;left:376px;top:13px;width:448px;height:45px;background:#fff;border:1px solid var(--line);border-radius:23px;display:flex;align-items:center;padding-left:24px;font-size:11px;color:var(--ink)}
.like-btn{display:flex;align-items:center;gap:4px;background:var(--teal);color:#fff;font-size:10px;font-weight:600;padding:2px 6px;border-radius:2px;margin:0 6px 0 74px}

/* footer */
.footer{height:405px;color:#fff;padding:30px 48px 0;position:relative}
.footer-cols{display:flex;justify-content:space-between}
.footer h4{font-size:17px;font-weight:600;margin-bottom:16px}
.footer-contact{width:270px;font-size:12.5px;line-height:20px}
.footer-contact p{margin-bottom:13px}
.footer-contact b{font-weight:600}
.footer-contact .email{font-size:12px;white-space:nowrap}
.footer-social{display:flex;gap:16px;margin-top:4px}
.footer-social span{width:11px;height:11px;border-radius:50%;background:var(--lime)}
.hq{width:520px;text-align:center}
.map{height:211px;background:linear-gradient(135deg,#d5ece6,#eef1ee 40%,#b7dcea 60%,#f1f3e3)}
.review{width:260px}
.review-quote{display:flex;gap:10px;font-size:12.5px;line-height:20px;font-weight:300}
.quote-mark{font-family:var(--head);font-size:50px;line-height:40px;font-weight:700;color:var(--lime)}
.reviewer{display:flex;align-items:center;gap:20px;margin-top:16px}
.avatar{width:78px;height:78px;border-radius:50%;background:linear-gradient(135deg,#e7ecd2,#b9d6d0)}
.reviewer strong{display:block;font-family:var(--head);font-size:16px;font-weight:500;margin-bottom:8px}
.reviewer small{font-size:12px}
.copyright{position:absolute;left:48px;right:48px;bottom:0;height:74px;border-top:1px solid rgba(255,255,255,.6);text-align:center;font-size:12px;font-weight:600;padding-top:24px}
</style>
</head>
<body>

<header class="hero">
  <div class="hero-photo" role="img" aria-label="Hand holding a small model house in front of a blurred home"></div>
  <div class="topbar">
    <div class="contact-item">
      <svg width="12" height="12" viewBox="0 0 24 24"><path fill="#fff" d="M6.6 10.8a15 15 0 006.6 6.6l2.2-2.2a1 1 0 011-.25 11.4 11.4 0 003.6.57 1 1 0 011 1V20a1 1 0 01-1 1A17 17 0 013 4a1 1 0 011-1h3.5a1 1 0 011 1c0 1.25.2 2.45.57 3.6a1 1 0 01-.25 1z"/></svg>
      +1 555-014-2290
    </div>
    <div class="contact-item">
      <svg width="14" height="11" viewBox="0 0 24 18"><rect x="1" y="1" width="22" height="16" rx="2" fill="none" stroke="#fff" stroke-width="2"/><path d="M1 2l11 8 11-8" fill="none" stroke="#fff" stroke-width="2"/></svg>
      info@pinecrestholdingsgroup.example
    </div>
    <div class="spacer"></div>
    <span class="sell-btn">Sell Your Home</span>
    <span class="social-dot"></span>
    <span class="social-dot"></span>
  </div>
  <div class="brand">
    <span class="brand-mark"></span>
    <span class="brand-name">PINECREST<br>HOLDINGS</span>
  </div>
  <nav class="nav">
    <span>HOME</span><span>ABOUT US</span><span>PORTFOLIO</span><span>BLOG</span><span>TESTIMONIALS</span><span>CONTACT US</span>
  </nav>
</header>

<section class="welcome band-gradient">
  <h1>Welcome We're Pinecrest Holdings Group</h1>
  <p>Pinecrest Holdings Group is a family run business with 3rd generation builders and renovators in the Morris County area. As the President and owner of Pinecrest Holdings Group I am dedicated to working hard to create opportunities for investment through real estate.</p>
  <p>At Pinecrest Holdings Group we have a valuable support system and a team of investors, realtors, attorneys, contractors and property managers providing a combined package offering years of experience in the local market.</p>
</section>

<section class="builders">
  <h2 class="section-title">Builders and <span>Renovators</span></h2>
  <div class="dotted-rule"></div>
  <div class="features">
    <div class="feature">
      <div class="feature-icon"><svg width="40" height="40" viewBox="0 0 40 40" fill="none" stroke="#fff" stroke-width="2"><path d="M6 18L20 7l14 11"/><path d="M10 16v16h20V16"/><rect x="15" y="20" width="10" height="7" rx="1"/></svg></div>
      <h3>What we do</h3>
      <p>We are a team of experienced home buyers and renovators in the Morris County, NJ area. Our specialty is purchasing distressed homes and property. We then collaborate with the best talents in Northern New Jersey to renovate those properties and transform them into the best house in the neighborhood.</p>
    </div>
    <div class="feature">
      <div class="feature-icon"><svg width="40" height="40" viewBox="0 0 40 40" fill="none" stroke="#fff" stroke-width="2"><path d="M20 35s-10-11-10-18a10 10 0 0120 0c0 7-10 18-10 18z"/><circle cx="20" cy="17" r="4"/></svg></div>
      <h3>Where we are</h3>
      <p>We only work in the Morris County area so we are local and know the area and market. We can finance or buy your home for cash. Our team will do any major renovations to the home or property and then make them available for rental or resale right here in our own neighborhoods.</p>
    </div>
    <div class="feature">
      <div class="feature-icon"><svg width="40" height="40" viewBox="0 0 40 40" fill="none" stroke="#fff" stroke-width="2"><path d="M10 5h14l6 6v24H10z"/><path d="M24 5v6h6M14 18h12M14 23h12M14 28h12"/></svg></div>
      <h3>Who we are</h3>
      <p>Pinecrest Holdings Group is a family run business with 3rd generation builders and renovators in the Morris County area. As the President and owner of Pinecrest Holdings Group I am dedicated to working hard to create opportunities for investment through real estate.</p>
    </div>
  </div>
</section>

<section class="mail-video">
  <div class="mail band-gradient">
    <h2>Feel Free to Mail</h2>
    <div class="field-row"><div class="field">Name *</div><div class="field">Email *</div></div>
    <div class="field">Subject</div>
    <div class="field message">Write Your Message Here...</div>
    <span class="send-btn">SEND MESSAGE</span>
  </div>
  <div class="video" role="img" aria-label="Intro video still of a lake under a cloudy sky">
    <svg class="play" width="134" height="134" viewBox="0 0 134 134"><circle cx="67" cy="67" r="60" fill="none" stroke="#fff" stroke-width="9"/><path d="M53 40l38 27-38 27z" fill="#fff"/></svg>
  </div>
</section>

<section class="work">
  <h2 class="section-title">Our <span>Work</span></h2>
  <div class="dotted-rule"></div>
  <div class="projects">
    <div class="project">
      <div class="project-photo" style="background:linear-gradient(180deg,#c9d3dd,#8a5a3c 45%,#6b4a34)" role="img" aria-label="Brick house under construction"></div>
      <h3>Denville New Build</h3>
      <p>Three-storey brick home framed and roofed, now moving into interior finishes.</p>
    </div>
    <div class="project">
      <div class="project-photo" style="background:linear-gradient(180deg,#d7d9dc,#b3a891 50%,#6f7358)" role="img" aria-label="Renovated two story house with stone wall"></div>
      <h3>Boonton Colonial</h3>
      <p>Full gut renovation with new siding, windows and a stone retaining wall.</p>
    </div>
    <div class="project">
      <div class="project-photo" style="background:linear-gradient(180deg,#6d8a4f,#c9c4ad 45%,#5e7a3d)" role="img" aria-label="Finished house with green lawn"></div>
      <h3>Parsippany Resale</h3>
      <p>Distressed home restored top to bottom and sold to a local family.</p>
    </div>
    <div class="project">
      <div class="project-photo" style="background:linear-gradient(180deg,#3f7fcf,#9ec1e6 45%,#8b7a63)" role="img" aria-label="New townhouse build site"></div>
      <h3>Rockaway Townhomes</h3>
      <p>Six-unit townhouse row in progress, open for investor partnership.</p>
    </div>
  </div>
</section>

<div class="like-bar">
  <div class="like-pill">
    <svg width="16" height="16" viewBox="0 0 24 24"><path fill="#c9d3d0" d="M2 10h4v11H2zM8 21h10l3-8v-3h-7l1-5-2-2-5 6z"/></svg>
    <span class="like-btn"><svg width="9" height="9" viewBox="0 0 10 10"><path d="M1 5l3 3 5-6" fill="none" stroke="#fff" stroke-width="2"/></svg>Like</span>
    You and 4.1k others like this.
  </div>
</div>

<footer class="footer band-gradient">
  <div class="footer-cols">
    <div class="footer-contact">
      <h4>Contact Us</h4>
      <p>Please feel free to contact us for any issue. Our staff is available to you from 9AM until 5PM on weekdays.</p>
      <p><b>Phone:</b> +1 (555) 013 48 62</p>
      <p><b>Office:</b> 418 Birchwood Lane, Morristown</p>
      <p class="email"><b>Email:</b> info@pinecrestholdingsgroup.example</p>
      <div class="footer-social"><span></span><span></span><span></span><span></span><span></span></div>
    </div>
    <div class="hq">
      <h4>Headquarters</h4>
      <div class="map" role="img" aria-label="Map showing the office location"></div>
    </div>
    <div class="review">
      <h4>Last Review</h4>
      <div class="review-quote"><span class="quote-mark">“</span><p>They bought our house quickly for a fair cash price and handled every detail. The renovated home now looks better than anything else on our street in Morris County.</p></div>
      <div class="reviewer">
        <div class="avatar" role="img" aria-label="Reviewer portrait"></div>
        <div><strong>Evan Marlow</strong><small>Home Seller</small></div>
      </div>
    </div>
  </div>
  <div class="copyright">Copyright 2020 - Pinecrest Holdings Group. All rights reserved.</div>
</footer>

</body>
</html>
```